Realtor branding business card

modern, simple and self branding. Broker office logo needs to be used but not emphasized. Looking to brand myself

Target Market(s)

buyers, sellers and investors

Industry/Entity Type

Realtor

Contact Information for Business Card

Sample of my current business card on file

Requirements
Must have
• my website - tobiasmerrowkl.com
• Realtor logo
• Fair housing logo
Nice to have
• Colors from office logo but not a must
Should not have
• Do not want headshot

```html
<!DOCTYPE html>
<html lang="en">
<head>
<meta charset="utf-8">
<title>Tobias Merrow – Realtor Business Card</title>
<link rel="stylesheet" href="https://fonts.googleapis.com/css2?family=Marcellus+SC&family=Open+Sans:wght@400;600&display=swap">
<style>
  :root {
    --backdrop: #3b3b3e;
    --card: #2a2a2c;
    --red: #e3262c;
    --red-deep: #b21d22;
    --ink: #ffffff;
    --ink-soft: #d9d9d9;
    --card-w: 630px;
    --card-h: 360px;
  }
  * { box-sizing: border-box; margin: 0; padding: 0; }
  html, body { width: 1200px; height: 900px; overflow: hidden; }
  body {
    background: var(--backdrop);
    font-family: "Open Sans", Arial, sans-serif;
    color: var(--ink);
    position: relative;
  }
  .card {
    position: absolute;
    left: 285px;
    width: var(--card-w);
    height: var(--card-h);
    background: var(--card);
    border-radius: 28px;
    overflow: hidden;
  }
  .card--front { top: 70px; }
  .card--back { top: 470px; }
  .card__band { position: absolute; left: 0; bottom: 0; width: 100%; height: 120px; }
  .card__band--back { height: 100px; }

  /* Front */
  .front__name {
    position: absolute; top: 118px; width: 100%; text-align: center;
    font-family: "Marcellus SC", Georgia, serif;
    font-size: 40px; font-weight: 400; letter-spacing: 1px; color: var(--ink);
  }
  .front__web {
    position: absolute; top: 190px; left: 230px;
    display: flex; align-items: center; gap: 14px;
  }
  .front__web-text {
    font-size: 17px; color: var(--ink-soft);
    border-bottom: 3px solid var(--red); padding: 0 8px 3px 4px;
  }

  /* Back */
  .back__name {
    position: absolute; top: 62px; left: 60px;
    font-size: 40px; font-weight: 400; letter-spacing: 0.5px; line-height: 1;
  }
  .back__title {
    position: absolute; top: 104px; left: 188px;
    font-size: 15px; letter-spacing: 0.5px; color: var(--ink-soft);
  }
  .brokerage {
    position: absolute; top: 200px; right: 34px;
    display: flex; align-items: center; gap: 8px;
    font-weight: 600; font-size: 17px; line-height: 1.1; color: var(--ink);
  }
  .brokerage__mark { width: 14px; height: 14px; background: var(--red); }
  .contact-list { position: absolute; top: 160px; left: 64px; list-style: none; }
  .contact-list li {
    display: flex; align-items: center; gap: 16px;
    font-size: 17px; line-height: 1.15; color: var(--ink-soft);
    margin-bottom: 12px;
  }
  .icon { width: 32px; height: 32px; flex: none; }
</style>
</head>
<body>

<section class="card card--front">
  <h1 class="front__name">Tobias Merrow</h1>
  <div class="front__web">
    <svg class="icon" viewBox="0 0 32 32" aria-hidden="true">
      <circle cx="16" cy="16" r="15" fill="var(--red)"/>
      <g fill="none" stroke="#2a2a2c" stroke-width="1.6">
        <circle cx="16" cy="16" r="9"/>
        <ellipse cx="16" cy="16" rx="4" ry="9"/>
        <line x1="7" y1="16" x2="25" y2="16"/>
        <line x1="9" y1="11" x2="23" y2="11"/>
        <line x1="9" y1="21" x2="23" y2="21"/>
      </g>
    </svg>
    <span class="front__web-text">keylinerealtykl.com</span>
  </div>
  <svg class="card__band" viewBox="0 0 630 120" preserveAspectRatio="none" aria-hidden="true">
    <rect x="0" y="98" width="630" height="22" fill="var(--red)"/>
    <polygon points="250,40 400,40 396,120 240,120" fill="var(--red-deep)"/>
    <polygon points="410,34 630,34 630,120 406,120" fill="var(--red)"/>
  </svg>
</section>

<section class="card card--back">
  <h2 class="back__name">TOBIAS MERROW , PA</h2>
  <p class="back__title">REALTOR</p>

  <div class="brokerage">
    <span class="brokerage__mark"></span>
    <span>Keyline<br>Realty Group</span>
  </div>

  <ul class="contact-list">
    <li>
      <svg class="icon" viewBox="0 0 32 32" aria-hidden="true">
        <path d="M16 3c-5.5 0-9.5 4-9.5 9.3 0 6.6 9.5 16.7 9.5 16.7s9.5-10.1 9.5-16.7C25.5 7 21.5 3 16 3z" fill="#fff"/>
        <circle cx="16" cy="12.5" r="3.6" fill="#2a2a2c"/>
      </svg>
      <span>482 Harlow Crest Dr.<br>Linden Park, FL 32790</span>
    </li>
    <li>
      <svg class="icon" viewBox="0 0 32 32" aria-hidden="true">
        <circle cx="16" cy="16" r="15" fill="var(--red)"/>
        <path d="M11 9.5l3 3-1.6 2.2c.9 1.9 2.1 3.1 4 4l2.2-1.6 3 3-2 2.3c-5.2-.7-10-5.5-10.7-10.7z" fill="#2a2a2c"/>
      </svg>
      <span>Cell: 407.555.0143<br>Office: 407.555.0188</span>
    </li>
    <li>
      <svg class="icon" viewBox="0 0 32 32" aria-hidden="true">
        <circle cx="16" cy="16" r="15" fill="var(--red)"/>
        <g fill="none" stroke="#2a2a2c" stroke-width="1.6">
          <circle cx="16" cy="16" r="9"/>
          <ellipse cx="16" cy="16" rx="4" ry="9"/>
          <line x1="7" y1="16" x2="25" y2="16"/>
        </g>
      </svg>
      <span>tobiasmerrowkl.com</span>
    </li>
  </ul>

  <svg class="card__band card__band--back" viewBox="0 0 630 100" preserveAspectRatio="none" aria-hidden="true">
    <rect x="0" y="80" width="630" height="20" fill="var(--red)"/>
    <polygon points="310,44 422,44 418,100 302,100" fill="var(--red-deep)"/>
    <polygon points="432,18 630,18 630,100 428,100" fill="var(--red)"/>
  </svg>
</section>

</body>
</html>
```